Personal Blog

The wordpress blog style and layout should be similar to http://www.samfenwick.com

homepage: my photo, list of things, call to action then 3 boxes (The Blog, The Book and podcast)

Other pages: About us, Blog, Consulting, Contact

Target Market(s)

Web Marketing Consultant

Industry/Entity Type

Consulting

Colors
3277b5
33a6d7
f04a50
f68e4e
33b7a4

```html
<!DOCTYPE html>
<html lang="en">
<head>
<meta charset="utf-8">
<title>Marek Lindqvist – Web Marketing Consultant</title>
<link rel="stylesheet" href="https://fonts.googleapis.com/css2?family=Dosis:wght@500;600;700&family=Arimo:ital,wght@0,400;0,700;1,400;1,700&display=swap">
<style>
:root{
  --orange:#f68e4e;
  --orange-dark:#e9782f;
  --ink:#222428;
  --text:#333;
  --muted:#777;
  --page:#eeeeee;
  --card:#ffffff;
  --rule:#dddddd;
  --band:#2c2f34;
  --band-dark:#24272b;
}
*{box-sizing:border-box;margin:0;padding:0}
html,body{width:1200px;height:3034px;overflow:hidden}
body{background:var(--page);font-family:"Arimo",Arial,sans-serif;color:var(--text);font-size:16px;line-height:1.45}
.site-header{height:185px;background:linear-gradient(var(--band),var(--band-dark));position:relative}
.brand{position:absolute;left:450px;top:30px;width:300px;height:82px;background:var(--orange);display:flex;align-items:center;justify-content:center;font-family:"Dosis",sans-serif;font-weight:600;font-size:40px;color:#fff;border-radius:4px}
.page{width:1110px;margin:0 auto;background:var(--card);height:2685px;position:relative;padding:0 48px}
.hero-title{font-family:"Dosis",sans-serif;font-weight:600;font-size:44px;line-height:1.08;text-align:center;color:var(--ink);padding-top:20px}
.hero-title em{font-style:normal;color:var(--orange)}
p{margin-bottom:16px}
.intro{padding-top:22px}
.lead-in{font-weight:700;color:#222}
.lead-in strong,.accent{color:var(--orange)}
.optin{display:flex;gap:32px;align-items:center;margin:26px 0 0;padding-left:8px}
.optin .field{width:330px;height:52px;border:1px solid #bbb;font-size:13px;padding:0 14px;display:flex;align-items:center;color:#444}
.optin .join{margin-left:auto;width:330px;height:56px;background:var(--orange);color:#fff;font-family:"Dosis",sans-serif;font-size:27px;font-weight:600;display:flex;align-items:center;justify-content:center;border-radius:3px}
.testimonial{margin:30px -48px 0;border-top:1px solid var(--rule);border-bottom:1px solid var(--rule);padding:22px 60px;text-align:center;font-family:"Dosis",sans-serif;font-weight:600;font-size:21px;line-height:1.3;color:#333}
.testimonial cite{font-family:"Arimo",sans-serif;font-size:13px;font-style:italic;color:var(--orange);font-weight:400}
.section-title{font-family:"Dosis",sans-serif;font-weight:600;font-size:28px;color:var(--ink);margin:38px 0 6px;letter-spacing:.5px}
.story{position:relative}
.story .narrow{padding-right:270px}
.portrait{position:absolute;right:10px;top:12px;width:240px;height:240px;border-radius:50%;border:5px solid var(--orange);background:radial-gradient(circle at 50% 40%,#f1f1f1,#cfd3d8 70%,#9aa1a9)}
.promo-title{font-family:"Dosis",sans-serif;font-weight:700;font-size:48px;color:var(--ink);margin:30px 0 18px}
.promo{display:flex;gap:30px;margin-bottom:26px;font-weight:700;color:#222;font-size:16px}
.promo .cover{flex:0 0 120px;height:190px;background:linear-gradient(160deg,#f4f4f2,#d8dcd6)}
.promo .cover.podcast{height:160px;background:linear-gradient(160deg,#c9442f,#6d6d6d 60%,#2d2d2d)}
.promo a,.promo i{color:var(--orange);font-style:italic}
.signoff{font-weight:700;color:#222;margin-top:10px}
.blog-link{text-align:center;font-weight:700;color:var(--orange);margin-top:36px;font-size:17px}
.site-footer{height:164px;background:linear-gradient(var(--band),var(--band-dark));display:flex;align-items:center;justify-content:center;color:#fff;font-size:14px}
.site-footer span{color:var(--orange);margin:0 4px}
</style>
</head>
<body>
<header class="site-header">
  <div class="brand">Marek Lindqvist</div>
</header>

<main class="page">
  <h1 class="hero-title">How this Site is Going to Make You<br><em>More Successful</em> in <em>Business</em> &amp; <em>Life</em></h1>

  <section class="intro">
    <p>"Lorem ipsum dolor sit amet, consectetur adipiscing elit, sed do eiusmod tempor incididunt ut labore et dolore magna aliqua. Ut enim ad minim veniam, quis nostrud exercitation ullamco laboris nisi ut aliquip ex ea commodo consequat.</p>
    <p>Duis aute irure dolor in reprehenderit in voluptate velit esse cillum dolore eu fugiat nulla pariatur. Excepteur sint occaecat cupidatat non proident, sunt in culpa qui officia deserunt mollit anim id est laborum.</p>
    <p>Sed ut perspiciatis unde omnis iste natus error sit voluptatem accusantium doloremque laudantium, totam rem aperiam, eaque ipsa quae ab illo inventore veritatis et quasi architecto beatae vitae dicta sunt explicabo. Nemo enim ipsam quia voluptas sit aspernatur aut odit aut fugit, sed quia consequuntur magni dolores eos qui ratione voluptatem sequi nesciunt.</p>
    <p>Neque porro quisquam est, qui dolorem ipsum quia dolor sit amet, consectetur, adipisci velit, sed quia non numquam eius modi tempora incidunt ut labore et dolore magnam aliquam quaerat voluptatem. Ut enim ad minima veniam, quis nostrum exercitationem ullam corporis suscipit laboriosam, nisi ut aliquid ex ea commodi consequatur?</p>
    <p class="lead-in">Enter your details below to get started by signing up for my <strong>FREE 7-Day</strong> 'New Business' Bootcamp.</p>
    <div class="optin"><div class="field">Enter your name...</div><div class="field">Enter your email...</div><div class="join">JOIN NOW! - FOR FREE!</div></div>
  </section>

  <blockquote class="testimonial">"I was blown away by his breadth of industry knowledge, the straight talking delivery and collaborative format.<br>A highly recommended social media expert and thought leader." <cite>- Tessa Marlowe - Marketing</cite></blockquote>

  <section class="story">
    <h2 class="section-title">MY STORY</h2>
    <div class="portrait" role="img" aria-label="Portrait photo of the consultant in a suit"></div>
    <div class="narrow">
      <p>"Lorem ipsum dolor sit amet, consectetur adipiscing elit, sed do eiusmod tempor incididunt ut labore et dolore magna aliqua. Ut enim ad minim veniam, quis nostrud exercitation ullamco laboris nisi ut aliquip ex ea commodo consequat.</p>
      <p>Duis aute irure dolor in reprehenderit in voluptate velit esse cillum dolore eu fugiat nulla pariatur.</p>
      <p>Excepteur sint occaecat cupidatat non proident, sunt in culpa qui officia deserunt mollit anim id est laborum. Sed ut perspiciatis unde omnis iste natus error sit voluptatem accusantium doloremque laudantium, totam rem aperiam, eaque ipsa quae.</p>
    </div>
    <p>Neque porro quisquam est, qui dolorem ipsum quia dolor sit amet, consectetur, adipisci velit, sed quia non numquam eius modi tempora incidunt ut labore et dolore magnam aliquam quaerat voluptatem.</p>
  </section>

  <blockquote class="testimonial">"I was blown away by his breadth of industry knowledge, the straight talking delivery and collaborative format.<br>A highly recommended social media expert and thought leader." <cite>- Tessa Marlowe - Marketing</cite></blockquote>

  <section>
    <h2 class="section-title">THE "NEW BUSINESS" MOMENT</h2>
    <p>"Lorem ipsum dolor sit amet, consectetur adipiscing elit, sed do eiusmod tempor incididunt ut labore et dolore magna aliqua. Ut enim ad minim veniam.</p>
    <p>Duis aute irure dolor in reprehenderit in voluptate velit esse cillum dolore eu fugiat nulla pariatur. Excepteur sint occaecat cupidatat non proident, sunt in culpa qui officia deserunt mollit anim id est laborum.</p>
    <p>Sed ut perspiciatis unde omnis iste natus error sit voluptatem accusantium doloremque laudantium, totam rem aperiam, eaque ipsa quae ab illo inventore veritatis et quasi architecto beatae vitae dicta sunt explicabo.</p>
    <p>Neque porro quisquam est, qui dolorem ipsum quia dolor sit amet</p>
    <p>Consectetur, adipisci velit, sed quia non numquam eius modi tempora incidunt ut labore et dolore magnam aliquam quaerat voluptatem. Ut enim ad minima veniam, quis nostrum exercitationem ullam corporis suscipit laboriosam, nisi ut aliquid ex ea commodi consequatur?</p>
    <p>So will you.</p>
  </section>

  <section>
    <h2 class="promo-title">Can't Miss, Shouldn't Miss!</h2>
    <div class="promo">
      <div class="cover" role="img" aria-label="Book cover of Remote Leverage"></div>
      <div>
        <p>My book, <i>Remote Leverage</i>: How to Work with Virtual Staff to Buy More Time, Become More Productive and Build Your Dream Business is the culmination of over a decade in the outsourcing industry and the result of working with thousands of entrepreneurs on their virtual team building strategies.</p>
        <p>It's available on <i>Bookhaven</i>, <i>Page &amp; Quill</i> and in every good bookstore around the world.</p>
      </div>
    </div>
    <div class="promo">
      <div class="cover podcast" role="img" aria-label="Growth Hour Podcast cover art"></div>
      <div>
        <p>The Growth Hour Podcast is very near and dear to my heart. Updated 2-4 times a month this show allows me to introduce you to the top minds in the 'new business' world. We discuss everything from strategy, growth, branding, launches, mindset and much more.</p>
        <p>Click <a>here</a> to listen on the blog, or <a>subscribe on PodStream</a>.</p>
      </div>
    </div>
    <p class="signoff">Thanks for dropping by, and be sure to join my <span class="accent">FREE 7-Day</span> 'New Business' Bootcamp. below.<br>I'll see you on the inside.</p>
    <div class="optin"><div class="field">Enter your name...</div><div class="field">Enter your email...</div><div class="join">JOIN NOW! - FOR FREE!</div></div>
  </section>

  <blockquote class="testimonial">"I was blown away by his breadth of industry knowledge, the straight talking delivery and collaborative format.<br>A highly recommended social media expert and thought leader." <cite>- Tessa Marlowe - Marketing</cite></blockquote>

  <p class="blog-link">Check Out My Blog</p>
</main>

<footer class="site-footer">© 2014 M. Lindqvist <span>www.mareklindqvist.com</span> | All Right Reserved.</footer>
</body>
</html>
```